Design logo, business cards, and web page for new web and bi development consulting company

I've started a Web and Business Intelligence development consulting company. We develop on Quordex's stack, Visual Sudio and Tabula Server. We develop responsive web sites and business intelligence platforms. I plan on focusing on small to medium sized business as my client base. I need a logo, business cards, and a one page web site. We will do more with the web site with you in the next six months if the business survives. The name of the company is Corvalo Integration Solutions, Corvalo for short.

Target Market(s)

small to medium sized businesses

Industry/Entity Type

Business

Contact Information for Business Card

logo
name
title
email
phone

Logo Text

Corvalo Integration Solutions - web and data solutions

Coding

Coded - Design and coding required

Number of Pages Required

1 page

Font styles to use
Sans Serif

Colors
0355a3
0092cd
00a88f
6b449b

Requirements
Nice to have
• web and data solutions

```html
<!DOCTYPE html>
<html lang="en">
<head>
<meta charset="utf-8">
<title>Corvalo Integration Solutions</title>
<link rel="stylesheet" href="https://fonts.googleapis.com/css2?family=Raleway:wght@400;500;600&family=Open+Sans:ital,wght@0,400;0,600;1,400&display=swap">
<style>
  :root {
    --navy: #0355a3;
    --sky: #0092cd;
    --teal: #00a88f;
    --green: #1a9a7a;
    --purple: #6b449b;
    --ink: #222;
    --body: #555;
    --footer: #e9e9e9;
    --white: #fff;
  }
  * { box-sizing: border-box; margin: 0; padding: 0; }
  html, body { width: 700px; height: 1200px; overflow: hidden; background: var(--white); }
  body { position: relative; font-family: "Open Sans", Arial, sans-serif; color: var(--body); }
  .abs { position: absolute; }

  /* Header */
  .site-header { top: 0; left: 0; width: 700px; height: 49px; border-bottom: 1px solid #e4e4e4; }
  .brand { left: 127px; top: 11px; font-family: "Raleway", sans-serif; font-weight: 500; font-size: 20px; color: var(--navy); }
  .main-nav { left: 303px; top: 22px; display: flex; gap: 21px; font-family: "Raleway", sans-serif; font-weight: 500; font-size: 7px; color: var(--ink); letter-spacing: .2px; }

  /* Hero */
  .hero-photo { top: 49px; left: 0; width: 700px; height: 275px; background: linear-gradient(100deg, #b9c9dc 0%, #8ea8c4 30%, #5b6f8c 50%, #8fa9cd 70%, #c6d6e8 100%); }
  .hero-card { left: 211px; top: 129px; width: 273px; height: 91px; background: rgba(0,146,205,.88); color: var(--white); text-align: center; padding-top: 13px; }
  .hero-title { font-family: "Raleway", sans-serif; font-size: 21px; font-weight: 400; }
  .hero-sub { font-family: "Raleway", sans-serif; font-size: 11px; margin-top: 2px; }
  .hero-text { font-size: 5.4px; line-height: 8px; margin: 6px 24px 0; }
  .hero-arrow { top: 162px; }

  /* About */
  .about { top: 357px; left: 0; width: 700px; text-align: center; }
  .about h2 { font-family: "Raleway", sans-serif; font-weight: 400; font-size: 17px; color: var(--ink); }
  .about .lead { font-family: "Raleway", sans-serif; font-size: 8px; color: #555; margin-top: 4px; }
  .about p.copy { font-size: 5.2px; line-height: 8.6px; width: 430px; margin: 8px auto 0; color: #666; }
  .about p.copy + p.copy { margin-top: 10px; }

  /* Services */
  .services-photo { top: 493px; left: 0; width: 700px; height: 199px; background: linear-gradient(90deg, #1e5cab 0%, #2f6fbe 35%, #1c58a8 65%, #3773bd 100%); }
  .services-title { top: 512px; left: 0; width: 700px; text-align: center; font-family: "Raleway", sans-serif; font-weight: 600; font-size: 11px; color: var(--white); }
  .service { top: 547px; width: 140px; text-align: center; color: var(--white); }
  .service .badge { width: 44px; height: 44px; border-radius: 50%; background: var(--white); margin: 0 auto; display: flex; align-items: center; justify-content: center; }
  .service h3 { font-family: "Raleway", sans-serif; font-weight: 500; font-size: 10.5px; margin-top: 5px; }
  .service p { font-size: 5.2px; line-height: 8px; margin-top: 1px; color: #e3ecf7; }
  .btn { display: inline-block; font-size: 6px; color: var(--white); padding: 4px 7px; }
  .btn-sky { background: var(--sky); margin-top: 7px; }
  .btn-purple { background: var(--purple); }

  /* Responsive */
  .responsive { top: 749px; left: 124px; width: 220px; }
  .responsive .kicker { font-family: "Raleway", sans-serif; font-size: 13px; color: var(--teal); }
  .responsive h2 { font-family: "Raleway", sans-serif; font-weight: 400; font-size: 19.5px; color: var(--purple); line-height: 1.1; }
  .responsive p { font-size: 5.2px; line-height: 8.4px; margin-top: 6px; color: #555; }
  .responsive .btn { margin-top: 7px; }
  .devices { top: 732px; left: 352px; width: 226px; height: 146px; border-radius: 4px; background: linear-gradient(135deg, #2a2f38 0%, #4a5566 45%, #d9dde3 100%); }

  /* Testimonials */
  .testimonials { top: 911px; left: 0; width: 700px; height: 167px; background: var(--green); color: var(--white); text-align: center; }
  .testimonials h2 { font-family: "Raleway", sans-serif; font-weight: 500; font-size: 13px; margin-top: 24px; }
  .avatar { width: 52px; height: 52px; border-radius: 50%; background: #c9a08a; border: 2px solid var(--white); margin: 8px auto 0; }
  .quote { font-style: italic; font-size: 5.8px; line-height: 10px; width: 300px; margin: 10px auto 0; color: #e8f5f1; }
  .author { font-size: 5.6px; margin-top: 3px; color: #e8f5f1; }

  /* Partners */
  .partners { top: 1078px; left: 0; width: 700px; height: 62px; display: flex; justify-content: center; align-items: center; gap: 24px; font-family: "Raleway", sans-serif; font-weight: 600; font-size: 10px; color: #3d4a5c; }

  /* Footer */
  .site-footer { top: 1140px; left: 0; width: 700px; height: 60px; background: var(--footer); }
  .footer-nav { left: 133px; top: 20px; font-size: 6px; color: #333; word-spacing: 1px; }
  .copyright { left: 133px; top: 33px; font-size: 5px; color: #555; }
  .social { left: 500px; top: 19px; display: flex; gap: 7px; font-family: "Raleway", sans-serif; font-weight: 600; font-size: 6.5px; color: #333; }
</style>
</head>
<body>

<header class="site-header abs">
  <div class="brand abs">Corvalo</div>
  <nav class="main-nav abs">
    <span>ABOUT US</span><span>SERVICES</span><span>PROJECTS</span><span>TESTIMONIAL</span><span>CONTACT</span>
  </nav>
</header>

<section class="hero">
  <div class="hero-photo abs" role="img" aria-label="Photo of two businessmen reviewing a tablet in a bright office"></div>
  <svg class="hero-arrow abs" style="left:94px" width="16" height="38" viewBox="0 0 16 38"><polyline points="14,1 2,19 14,37" fill="none" stroke="#1d4f8f" stroke-width="1.6"/></svg>
  <svg class="hero-arrow abs" style="left:588px" width="16" height="38" viewBox="0 0 16 38"><polyline points="2,1 14,19 2,37" fill="none" stroke="#1d4f8f" stroke-width="1.6"/></svg>
  <div class="hero-card abs">
    <h1 class="hero-title">Web and Data Solutions</h1>
    <div class="hero-sub">Responsive sites and business intelligence</div>
    <p class="hero-text">We plan, build and run web and data platforms for growing firms. Clear scope, steady delivery and honest support.</p>
  </div>
</section>

<section class="about abs">
  <h2>About Our Company</h2>
  <p class="lead">Corvalo Integration Solutions builds web and data platforms for small and medium businesses</p>
  <p class="copy">We are a small team of developers who build web sites and business intelligence tools for small and medium sized firms. We listen first, then design systems that fit the way you already work, so your staff can adopt them quickly and keep using them with confidence.</p>
  <p class="copy">Every project starts with a short discovery phase where we map your data, your goals and your budget. From there we deliver in clear stages, share progress each week and hand over clean, documented code that your own team can maintain long after launch.</p>
</section>

<section class="services">
  <div class="services-photo abs" role="img" aria-label="Blue-tinted photo of a business team meeting around a table"></div>
  <h2 class="services-title abs">SERVICES PROVIDES</h2>
  <div class="service abs" style="left:125px">
    <div class="badge">
      <svg width="24" height="24" viewBox="0 0 24 24" aria-hidden="true">
        <polygon points="12,14 22,18 12,22 2,18" fill="var(--teal)"/>
        <polygon points="12,8 22,12 12,16 2,12" fill="var(--sky)"/>
        <polygon points="12,2 22,6 12,10 2,6" fill="var(--navy)"/>
      </svg>
    </div>
    <h3>Quordex's stack</h3>
    <p>Modern tools for fast, secure builds that grow with your business and stay simple to maintain over time.</p>
    <span class="btn btn-sky">Read More</span>
  </div>
  <div class="service abs" style="left:278px">
    <div class="badge">
      <svg width="26" height="22" viewBox="0 0 26 22" aria-hidden="true" fill="none" stroke="var(--purple)" stroke-width="2.4" stroke-linecap="round" stroke-linejoin="round">
        <polyline points="8,5 2,11 8,17"/>
        <polyline points="18,5 24,11 18,17"/>
        <line x1="15" y1="3" x2="11" y2="19"/>
      </svg>
    </div>
    <h3>Lumen Studio</h3>
    <p>Clean, tested code written in a proven environment, with steady releases and clear notes for every change.</p>
    <span class="btn btn-sky">Read More</span>
  </div>
  <div class="service abs" style="left:433px">
    <div class="badge">
      <svg width="22" height="26" viewBox="0 0 22 26" aria-hidden="true">
        <path d="M2 5v16c0 2.2 4 4 9 4s9-1.8 9-4V5" fill="var(--sky)"/>
        <ellipse cx="11" cy="5" rx="9" ry="4" fill="var(--navy)"/>
        <path d="M2 11c0 2.2 4 4 9 4s9-1.8 9-4M2 16c0 2.2 4 4 9 4s9-1.8 9-4" fill="none" stroke="#fff" stroke-width="1.2"/>
      </svg>
    </div>
    <h3>Tabula Server</h3>
    <p>Reliable databases and reports that turn daily records into numbers your team can read and act on.</p>
    <span class="btn btn-sky">Read More</span>
  </div>
</section>

<section class="responsive abs">
  <div class="kicker">Developed Responsive</div>
  <h2>Website Templates</h2>
  <p>Every site we build adapts to phones, tablets and desktops without losing speed or clarity. Your customers get the same smooth experience wherever they find you.</p>
  <p>We test on real devices and tune each layout before launch, so nothing breaks when traffic grows.</p>
  <span class="btn btn-purple">View More</span>
</section>
<div class="devices abs" role="img" aria-label="Illustration of a website shown on a desktop monitor, tablet and phone"></div>

<section class="testimonials abs">
  <svg class="abs" style="left:163px;top:32px" width="14" height="32" viewBox="0 0 14 32"><polyline points="12,1 2,16 12,31" fill="none" stroke="#fff" stroke-width="1.2"/></svg>
  <svg class="abs" style="left:530px;top:32px" width="14" height="32" viewBox="0 0 14 32"><polyline points="2,1 12,16 2,31" fill="none" stroke="#fff" stroke-width="1.2"/></svg>
  <h2>TESTIMONIALS</h2>
  <div class="avatar" role="img" aria-label="Portrait photo of the client giving the testimonial"></div>
  <p class="quote">“ They rebuilt our ordering site and reporting in eight weeks. The dashboards are easy to read, the pages load fast on every phone, and support answers the same day whenever we ask a question. ”</p>
  <p class="author">By Author Name, City Location</p>
</section>

<section class="partners abs">
  <span>Netframe</span><span>Searchly</span><span>Hartwell Grove</span><span>Tessara</span><span>Lumen Studio</span><span>Tabula Server</span>
</section>

<footer class="site-footer abs">
  <div class="footer-nav abs">HOME &nbsp;|&nbsp; ABOUT &nbsp;|&nbsp; SERVICES &nbsp;|&nbsp; TESTIMONIALS &nbsp;|&nbsp; CLIENTS &nbsp;|&nbsp; CONTACT</div>
  <div class="copyright abs">© 2015 Corvalo Integration Solutions &nbsp;All right reserved &nbsp;Term of Use</div>
  <div class="social abs"><span>Chirpline</span><span>Facely</span><span>Linkwork</span></div>
</footer>

</body>
</html>
```